Corporate-Design für Osteopathie-Praxis
Das Corporate Design war sehr gut, Änderungswünsche wurden zügig und exakt umgesetzt. Die Designerin stand auch nach der Siegerehrung immer zur Verfügung und hat weitere kleine Änderungen problemlos vorgenommen. Die Zusammenarbeit war immer angenehm und ist nur zu empfehlen.
Zielgruppe
Wir sind eine neue Osteopathie Praxis mit einem Klientel von Jung bis Alt. Vorwiegend etwas gut situiertere Personen. Es soll daher exklusiv aber auch hip sein, da unser Ziel darin besteht eine sehr moderne und edle Praxis aufzubauen.
Aufgabenstellung
Die Praxis soll den Namen „Lumen“ bekommen. Aus zwei Gründen;
die Praxis befindet sich an der Küste in Kiel. Ich möchte hier eine Verbindung zum Standort schaffen. Zweitens sind in dem Namen „Lumen“ meine Initialen LM sowie die Abkürzung für Osteopathie, ost. , vorhanden. Wenn man diese Ideen in dem Logo wiederfinden könnte, wäre es sehr schön. Die Farben blau, weiß, grau richten sich an den skandinavisch-maritimen Stil dem ich folgen möchte. Ich möchte hierbei aber klassisch (nicht verspielt wie zB mit einem Leuchtturm im Logo), etwas exklusiv und hip sein. Es darf aber auch nicht zu abstrakt sein, sodass auch ältere Kunden den Namen/das Logo lesen können

```html
<!DOCTYPE html>
<html lang="de">
<head>
<meta charset="utf-8">
<title>Lumen – Corporate Design</title>
<link href="https://fonts.googleapis.com/css2?family=Open+Sans:wght@300;400;600&family=Roboto:wght@400;700&display=swap" rel="stylesheet">
<style>
  :root {
    --teal: #6fbccb;
    --teal-light: #c4e3e8;
    --dark-grey: #575756;
    --light-grey: #9d9d9c;
    --swatch-dark: #707070;
    --swatch-light: #b2b2b2;
    --contact: #7fa6ad;
    --paper: #ffffff;
  }
  * { margin: 0; padding: 0; box-sizing: border-box; }
  html, body { width: 1200px; height: 1200px; overflow: hidden; background: var(--paper); }
  body { position: relative; font-family: "Open Sans", sans-serif; }

  .swatch { position: absolute; top: 142px; width: 207px; height: 40px; }
  .swatch--gradient { left: 401px; background: linear-gradient(90deg, var(--teal-light), var(--teal)); }
  .swatch--dark { left: 630px; background: var(--swatch-dark); }
  .swatch--light { left: 859px; background: var(--swatch-light); }
  .swatch-label {
    position: absolute; top: 196px; width: 207px; text-align: center;
    font-family: "Roboto", sans-serif; font-weight: 700; font-size: 12.5px; color: #8a8a8a;
  }

  .brand-name {
    position: absolute; font-family: "Open Sans", sans-serif; font-weight: 300;
    color: var(--teal); text-align: center; letter-spacing: 2px;
  }
  .brand-name--main { left: 484px; top: 270px; width: 400px; font-size: 92px; line-height: 1; }
  .brand-tagline {
    position: absolute; font-weight: 400; color: var(--dark-grey);
    text-align: center; letter-spacing: 1.5px; white-space: nowrap;
  }
  .brand-tagline--main { left: 484px; top: 408px; width: 400px; font-size: 22px; }
  .brand-subline {
    position: absolute; left: 484px; top: 434px; width: 400px; text-align: center;
    font-weight: 300; font-size: 17px; color: var(--light-grey); letter-spacing: 1.3px;
  }

  .card {
    position: absolute; width: 454px; height: 301px; background: var(--paper);
    border: 1px solid #e6e6e6; box-shadow: 4px 5px 7px rgba(0,0,0,0.28); overflow: hidden;
  }
  .card--front { left: 127px; top: 560px; }
  .card--back { left: 625px; top: 704px; }

  .card__name { position: absolute; top: 62px; width: 100%; text-align: center; font-size: 27px; color: var(--dark-grey); }
  .card__role { position: absolute; top: 97px; width: 100%; text-align: center; font-size: 13.5px; color: var(--dark-grey); letter-spacing: 1.6px; }
  .card__qual { position: absolute; width: 100%; text-align: center; font-weight: 300; font-size: 13.5px; color: var(--light-grey); letter-spacing: 1.5px; }
  .card__qual--one { top: 128px; }
  .card__qual--two { top: 147px; }

  .card__contact { position: absolute; font-family: "Roboto", sans-serif; font-size: 12.5px; line-height: 16px; color: var(--contact); }
  .card__contact--address { left: 78px; top: 196px; }
  .card__contact--reach { left: 254px; top: 195px; letter-spacing: 0.3px; }
  .card__band { position: absolute; left: 0; bottom: 0; width: 100%; height: 20px; background: linear-gradient(90deg, #eef5f5, #d8e9e8 45%, #acd5de); }

  .brand-name--card { left: 77px; top: 90px; width: 300px; font-size: 92px; line-height: 1; }
  .brand-tagline--card { left: 0; top: 226px; width: 100%; font-size: 26px; letter-spacing: 2px; }
</style>
</head>
<body>
  <div class="swatch swatch--gradient"></div>
  <div class="swatch swatch--dark"></div>
  <div class="swatch swatch--light"></div>
  <div class="swatch-label" style="left:386px"># Verlauf</div>
  <div class="swatch-label" style="left:620px">#575756</div>
  <div class="swatch-label" style="left:859px">#9D9D9C</div>

  <div class="brand-name brand-name--main">Lumen</div>
  <div class="brand-tagline brand-tagline--main">Praxis für Osteopathie</div>
  <div class="brand-subline">Lukas Mertens – Heilpraktiker</div>

  <section class="card card--front">
    <div class="card__name">Lukas Mertens</div>
    <div class="card__role">Heilpraktiker für</div>
    <div class="card__qual card__qual--one">BSc Osteopathie &nbsp;– Faszium Therapie</div>
    <div class="card__qual card__qual--two">NSVK Sportphysiotherapie</div>
    <div class="card__contact card__contact--address">Lumen<br>StreetStreetStreet 000<br>00000 CityCity</div>
    <div class="card__contact card__contact--reach">Tel.&nbsp; 43 17 / 88 31 00<br>Fax&nbsp; 43 17 / 88 31 09<br>info@lumenpraxis.info<br>www.lumenpraxis.de</div>
    <div class="card__band"></div>
  </section>

  <section class="card card--back">
    <div class="brand-name brand-name--card">Lumen</div>
    <div class="brand-tagline brand-tagline--card">Praxis für Osteopathie</div>
  </section>
</body>
</html>
```